VOMRA Pty Ltd Business Card

Looking for a simple yet eye-catching double-sided business card design using my company logo on one side and contact details on the other.

Target Market(s)

Government

Industry/Entity Type

Communication Systems Engineering

Contact Information for Business Card

VOMRA Pty Ltd

Requirements
Nice to have
• Would be great to have a QR code so details can be scanned into contacts

```html
<!DOCTYPE html>
<html lang="en">
<head>
<meta charset="utf-8">
<title>VOMRA Pty Ltd Business Card</title>
<link rel="stylesheet" href="https://fonts.googleapis.com/css2?family=Montserrat:wght@400;500;700;800&display=swap">
<style>
  :root {
    --slate: #37424a;
    --ink: #2e363d;
    --black: #0b0b0b;
    --paper: #ffffff;
    --backdrop: #e9eaec;
    --shadow: rgba(20, 26, 32, 0.18);
  }
  * { box-sizing: border-box; margin: 0; padding: 0; }
  html, body {
    width: 1200px; height: 960px; overflow: hidden;
    background: var(--backdrop);
    font-family: "Montserrat", Arial, sans-serif;
  }
  .canvas { position: relative; width: 1200px; height: 960px; }
  .card {
    position: absolute; left: 260px;
    width: 680px; height: 388px;
    border-radius: 26px; overflow: hidden;
    box-shadow: 0 10px 30px var(--shadow);
  }
  .card--back { top: 52px; background: var(--slate); }
  .card--front { top: 500px; background: var(--paper); }

  .brand { position: absolute; display: flex; align-items: center; }
  .brand__dot { border-radius: 50%; flex: none; }
  .brand__name { font-weight: 800; line-height: 1; white-space: nowrap; }

  .card--back .brand { left: 0; right: 0; top: 0; bottom: 0; justify-content: center; gap: 22px; }
  .card--back .brand__dot { background: var(--paper); width: 74px; height: 74px; }
  .card--back .brand__name { color: var(--paper); font-size: 92px; letter-spacing: 4px; }

  .card--front .brand { left: 40px; top: 150px; gap: 16px; }
  .card--front .brand__dot { background: var(--ink); width: 40px; height: 40px; }
  .card--front .brand__name { color: var(--ink); font-size: 48px; letter-spacing: 3px; }

  .divider {
    position: absolute; left: 372px; top: 78px;
    width: 1.5px; height: 205px; background: var(--ink);
  }
  .contact {
    position: absolute; left: 396px; top: 72px; width: 270px;
    color: var(--ink);
  }
  .contact__name {
    font-weight: 800; font-size: 23px; letter-spacing: 0.5px; text-transform: uppercase;
  }
  .contact__role { font-weight: 400; font-size: 15px; margin-top: 2px; }
  .contact__list { list-style: none; margin-top: 18px; }
  .contact__item {
    display: flex; align-items: center; gap: 9px;
    font-size: 14.5px; line-height: 24px;
  }
  .contact__item svg { width: 14px; height: 14px; flex: none; }
  .contact__address {
    font-style: normal; font-size: 14.5px; line-height: 21px; margin-top: 14px;
  }
  .wave { position: absolute; left: 0; top: 0; width: 680px; height: 388px; }
</style>
</head>
<body>
<main class="canvas">

  <section class="card card--back" aria-label="Card back">
    <div class="brand">
      <span class="brand__dot"></span>
      <span class="brand__name">VOMRA</span>
    </div>
  </section>

  <section class="card card--front" aria-label="Card front">
    <svg class="wave" viewBox="0 0 680 388" preserveAspectRatio="none" aria-hidden="true">
      <path d="M0,340 C230,336 420,304 680,288 L680,300 C420,318 230,352 0,354 Z" fill="var(--black)"/>
      <path d="M0,360 C230,358 420,324 680,308 L680,388 L0,388 Z" fill="var(--slate)"/>
    </svg>

    <div class="brand">
      <span class="brand__dot"></span>
      <span class="brand__name">VOMRA</span>
    </div>

    <div class="divider"></div>

    <div class="contact">
      <h1 class="contact__name">Daniel Hartley</h1>
      <p class="contact__role">Managing Director</p>
      <ul class="contact__list">
        <li class="contact__item">
          <svg viewBox="0 0 16 16"><path d="M3.5 1.5l3 3-1.8 1.8c.8 1.9 2.2 3.3 4.1 4.1l1.8-1.8 3 3-2 2C6.6 13.6 2.4 9.4 1.5 3.5z" fill="var(--ink)"/></svg>
          <span>987 654 321</span>
        </li>
        <li class="contact__item">
          <svg viewBox="0 0 16 16"><rect x="1" y="3" width="14" height="10" rx="1" fill="var(--ink)"/><path d="M1.5 3.8L8 8.8l6.5-5" stroke="var(--paper)" stroke-width="1.3" fill="none"/></svg>
          <span>admin@vomra.com.au</span>
        </li>
        <li class="contact__item">
          <svg viewBox="0 0 16 16"><circle cx="8" cy="8" r="7" fill="var(--ink)"/><path d="M1 8h14M8 1c-3 3.5-3 10.5 0 14M8 1c3 3.5 3 10.5 0 14" stroke="var(--paper)" stroke-width="1" fill="none"/></svg>
          <span>www.vomra.com.au</span>
        </li>
      </ul>
      <address class="contact__address">42-44 Harbour Lane Glenmore<br>NSW 2150 Australia</address>
    </div>
  </section>

</main>
</body>
</html>
```